MRT Property - Business Cards

Looking for a business card & general letterhead, signage etc design for our new logo.

Colours:
000a20
0056a2
00b5ef
0088ce
68cef2

Fonts:
Poppins
Karla

Please keep look and feel of new brand - example in the zip package I sent.

```html
<!DOCTYPE html>
<html lang="en">
<head>
<meta charset="utf-8">
<title>MRT Property – Stationery</title>
<link rel="stylesheet" href="https://fonts.googleapis.com/css2?family=Poppins:wght@400;500;600;700&family=Karla:wght@400;600&display=swap">
<style>
  :root{
    --ink:#000a20;
    --navy:#0056a2;
    --cyan:#00b5ef;
    --mid:#0088ce;
    --sky:#68cef2;
    --paper:#ffffff;
    --stage:#8c8c8c;
  }
  *{box-sizing:border-box;margin:0;padding:0}
  html,body{width:1200px;height:686px;overflow:hidden;background:var(--stage)}
  body{position:relative;font-family:"Poppins",sans-serif;color:var(--ink)}

  .sheet{position:absolute;background:var(--paper);overflow:hidden;box-shadow:0 6px 18px rgba(0,0,0,.25)}
  .wave{position:absolute;inset:0;width:100%;height:100%}

  .brand{font-family:"Poppins",sans-serif;font-weight:700;color:var(--navy);letter-spacing:.5px;display:flex;align-items:center;gap:8px;white-space:nowrap}
  .brand-dot{border-radius:50%;background:var(--navy);flex:none}

  /* Letterhead */
  .letterhead{left:40px;top:33px;width:440px;height:620px}
  .letterhead .brand{position:absolute;right:34px;top:40px;font-size:26px}
  .letterhead .brand-dot{width:16px;height:16px}
  .letterhead .contact{position:absolute;right:34px;top:104px;width:190px;padding-left:14px;border-left:1.5px solid var(--mid)}

  .contact-list{list-style:none;font-size:10px;line-height:1.55;color:var(--ink)}
  .contact-list li{display:flex;align-items:flex-start;gap:6px}
  .contact-list svg{width:9px;height:9px;flex:none;margin-top:3px;fill:var(--mid)}
  .contact-list .address{margin-top:4px}

  /* Business cards */
  .card{left:600px;width:480px;height:274px}
  .card-front{top:50px}
  .card-back{top:362px;display:flex;align-items:center;justify-content:center}
  .card-back .brand{font-size:40px}
  .card-back .brand-dot{width:24px;height:24px}

  .card-front .brand{position:absolute;left:34px;top:38px;font-size:22px}
  .card-front .brand-dot{width:13px;height:13px}
  .card-front .divider{position:absolute;left:228px;top:40px;width:1px;height:130px;background:var(--mid)}
  .card-front .person{position:absolute;left:250px;top:40px}
  .person-name{font-family:"Karla",sans-serif;font-size:24px;line-height:1.1;font-weight:600;color:var(--navy)}
  .person-name .surname{font-weight:400;color:var(--sky)}
  .person-role{font-size:10px;font-weight:500;margin-top:2px}
  .card-front .contact-list{margin-top:12px}
  .card-front .address-band{position:absolute;left:22px;bottom:14px;font-size:10px;line-height:1.2;color:var(--paper);letter-spacing:.2px;white-space:nowrap}
</style>
</head>
<body>

<section class="sheet letterhead" aria-label="Letterhead">
  <svg class="wave" viewBox="0 0 440 620" preserveAspectRatio="none" aria-hidden="true">
    <path d="M0 390 C 30 480 150 540 225 620 L0 620 Z" fill="var(--navy)"/>
    <path d="M0 380 C 30 470 165 530 245 620" fill="none" stroke="var(--sky)" stroke-width="5"/>
  </svg>
  <div class="brand"><span class="brand-dot"></span>MRT Property</div>
  <div class="contact">
    <ul class="contact-list">
      <li><svg viewBox="0 0 10 10"><path d="M2 0h2l1 3-1.5 1a6 6 0 0 0 2.5 2.5L7 5l3 1v2c0 1-1 2-2 2A8 8 0 0 1 0 2c0-1 1-2 2-2z"/></svg>+61 2 5550 1234</li>
      <li><svg viewBox="0 0 10 10"><circle cx="5" cy="5" r="5"/></svg>www.mrtproperty.com.au</li>
      <li><svg viewBox="0 0 10 10"><rect y="2" width="10" height="7" rx="1"/></svg>info@mrtproperty.com.au</li>
      <li class="address"><svg viewBox="0 0 10 10"><path d="M5 0a3.5 3.5 0 0 1 3.5 3.5C8.5 6 5 10 5 10S1.5 6 1.5 3.5A3.5 3.5 0 0 1 5 0z"/></svg><span>Suite 4.12, Block 3<br>18 Harbourline Road<br>Riverside Park NSW 2150</span></li>
    </ul>
  </div>
</section>

<section class="sheet card card-front" aria-label="Business card front">
  <svg class="wave" viewBox="0 0 480 274" preserveAspectRatio="none" aria-hidden="true">
    <path d="M0 206 C 160 212 330 228 480 250 L480 274 L0 274 Z" fill="var(--navy)"/>
    <path d="M0 197 C 160 203 330 219 480 241" fill="none" stroke="var(--sky)" stroke-width="4"/>
  </svg>
  <div class="brand"><span class="brand-dot"></span>MRT Property</div>
  <div class="divider"></div>
  <div class="person">
    <p class="person-name">Liam <span class="surname">Harwood</span></p>
    <p class="person-role">Director</p>
    <ul class="contact-list">
      <li><svg viewBox="0 0 10 10"><path d="M2 0h2l1 3-1.5 1a6 6 0 0 0 2.5 2.5L7 5l3 1v2c0 1-1 2-2 2A8 8 0 0 1 0 2c0-1 1-2 2-2z"/></svg>+61 2 5550 1234</li>
      <li><svg viewBox="0 0 10 10"><circle cx="5" cy="5" r="5"/></svg>www.mrtproperty.com.au</li>
      <li><svg viewBox="0 0 10 10"><rect y="2" width="10" height="7" rx="1"/></svg>info@mrtproperty.com.au</li>
    </ul>
  </div>
  <p class="address-band">Suite 4.12, Block 3, 18 Harbourline Road, Riverside Park NSW 2150</p>
</section>

<section class="sheet card card-back" aria-label="Business card back">
  <div class="brand"><span class="brand-dot"></span>MRT Property</div>
</section>

</body>
</html>
```